Harborview Estates Business Card for Apartment Buildings

Create business cards for resident managers who run apartment buildings. The audience is the public who are searching for apartment rentals, and current residents who live at the apartment building. Key design element will be incorporating the company logo, however, the logo cannot dominate. The building name and manager name are more important than the logo. Current business card design leaves little room for copy, so we may need to reduce the size on the current card to allow for more space for copy.

Target Market(s)

Adults 18-65 years of age, who are looking for an apartment rental, plus current residents who live at our apartment buildings.

Industry/Entity Type

Property Management

Contact Information for Business Card

A major design element will be use of the company logo. Important property and manager contact information must be part of the design. The size of the logo will need to be reduced to make room for building and manager contact copy.

Font styles to use
Sans Serif

Colors
3176b5
000000
959595
ffffff

Requirements
Must have
• 1) Incorporate the company logo.
• 2) Use the company colors (dark blue, black/grey, over white).
• 3) FEATURE THE BUILDING NAME
• 4) FEATURE THE MANAGER NAME
• 5) The company name is less important than BUILDING and MANAGER
• 6) Manager contact information
• **SEE ATTACHED CREATIVE BRIEF**
Nice to have
• 1) Back of card logo watermark
• 2) Ability to write notes on back of carfd
Should not have
• Avoid letting the company logo dominate the card, the building name and manager are more important than the company logo.

```html
<!DOCTYPE html>
<html lang="en">
<head>
<meta charset="utf-8">
<title>Harborview Estates – Resident Manager Business Card</title>
<link rel="stylesheet" href="https://fonts.googleapis.com/css2?family=Open+Sans:wght@300;400;600;700&display=swap">
<style>
  :root {
    --brand-blue: #1a6aa8;
    --brand-grey: #48494b;
    --text-grey: #5a5a5a;
    --rule-grey: #7d7d7d;
    --paper: #ffffff;
    --paper-back: #e4e6e7;
    --stage: #a3a3a3;
  }
  * { box-sizing: border-box; margin: 0; padding: 0; }
  html, body {
    width: 1200px; height: 1200px; overflow: hidden;
    background: var(--stage);
    font-family: "Open Sans", Arial, sans-serif;
  }
  .card {
    position: absolute;
    left: 206px;
    width: 788px;
    height: 450px;
  }
  .card--front { top: 94px; background: var(--paper); }
  .card--back { top: 656px; background: var(--paper-back); }

  .front-info {
    position: absolute;
    right: 42px;
    top: 38px;
    text-align: right;
  }
  .building-name {
    font-size: 43px;
    font-weight: 700;
    color: var(--brand-blue);
    letter-spacing: 0.2px;
    line-height: 1.2;
  }
  .building-address {
    margin-top: 8px;
    margin-right: 40px;
    font-size: 19px;
    font-weight: 300;
    color: var(--text-grey);
    line-height: 32px;
  }
  .manager-name {
    margin-top: 14px;
    margin-right: 40px;
    font-size: 26px;
    font-weight: 700;
    color: var(--brand-blue);
    line-height: 1.3;
  }
  .manager-role {
    margin-right: 40px;
    font-size: 19px;
    color: var(--text-grey);
    line-height: 1.4;
  }
  .contact-list {
    list-style: none;
    margin-top: 20px;
  }
  .contact-item {
    display: flex;
    justify-content: flex-end;
    align-items: center;
    gap: 14px;
    font-size: 18px;
    font-weight: 300;
    color: var(--text-grey);
    line-height: 31px;
  }
  .contact-item .accent { color: var(--brand-blue); font-weight: 400; }
  .contact-icon { width: 18px; height: 18px; flex: none; }
  .edge-tab {
    position: absolute;
    right: 0;
    top: 175px;
    width: 10px;
    height: 62px;
    background: var(--brand-blue);
  }

  .company-mark {
    position: absolute;
    left: 40px;
    top: 58px;
    display: flex;
    align-items: center;
    gap: 12px;
  }
  .company-mark__square {
    width: 40px; height: 40px;
    background: var(--brand-blue);
  }
  .company-mark__name {
    font-size: 28px;
    font-weight: 700;
    color: var(--brand-blue);
    letter-spacing: 1px;
  }
  .note-lines {
    position: absolute;
    left: 40px;
    right: 38px;
    top: 173px;
  }
  .note-line {
    height: 42px;
    border-top: 1px solid var(--rule-grey);
  }
</style>
</head>
<body>
  <section class="card card--front" aria-label="Business card front">
    <div class="front-info">
      <h1 class="building-name">Bayside Court Apartments</h1>
      <p class="building-address">2845 Cedar Lane San<br>Diego, CA 92110</p>
      <h2 class="manager-name">Marisol Vega</h2>
      <p class="manager-role">Resident Manager</p>
      <ul class="contact-list">
        <li class="contact-item">555-210-4830
          <svg class="contact-icon" viewBox="0 0 24 24" aria-label="Phone"><path fill="#1a6aa8" d="M6.6 10.8a15.2 15.2 0 0 0 6.6 6.6l2.2-2.2a1 1 0 0 1 1-.25 11.4 11.4 0 0 0 3.6.57 1 1 0 0 1 1 1V20a1 1 0 0 1-1 1A17 17 0 0 1 3 4a1 1 0 0 1 1-1h3.5a1 1 0 0 1 1 1c0 1.25.2 2.45.57 3.57a1 1 0 0 1-.25 1z"/></svg>
        </li>
        <li class="contact-item">555-210-4831
          <svg class="contact-icon" viewBox="0 0 24 24" aria-label="Fax"><path fill="#1a6aa8" d="M7 3h10v5H7zM4 9h16a2 2 0 0 1 2 2v6h-4v4H6v-4H2v-6a2 2 0 0 1 2-2zm4 6v4h8v-4z"/></svg>
        </li>
        <li class="contact-item">555-376-9042
          <svg class="contact-icon" viewBox="0 0 24 24" aria-label="Mobile"><path fill="none" stroke="#1a6aa8" stroke-width="2" d="M7 2.5h10a1 1 0 0 1 1 1v17a1 1 0 0 1-1 1H7a1 1 0 0 1-1-1v-17a1 1 0 0 1 1-1z"/><circle cx="12" cy="18" r="1.2" fill="#1a6aa8"/></svg>
        </li>
        <li class="contact-item">marisol@harborviewest.com
          <svg class="contact-icon" viewBox="0 0 24 24" aria-label="Email"><rect x="2.5" y="5" width="19" height="14" fill="none" stroke="#1a6aa8" stroke-width="2"/><path d="M3 6l9 7 9-7" fill="none" stroke="#1a6aa8" stroke-width="2"/></svg>
        </li>
        <li class="contact-item"><span>www.<span class="accent">harborviewest</span>.com</span>
          <svg class="contact-icon" viewBox="0 0 24 24" aria-label="Website"><circle cx="12" cy="12" r="9.5" fill="none" stroke="#1a6aa8" stroke-width="2"/><path d="M2.5 12h19M12 2.5c3 3 3 16 0 19M12 2.5c-3 3-3 16 0 19" fill="none" stroke="#1a6aa8" stroke-width="1.6"/></svg>
        </li>
      </ul>
    </div>
    <div class="edge-tab"></div>
  </section>

  <section class="card card--back" aria-label="Business card back with note lines">
    <div class="company-mark">
      <span class="company-mark__square"></span>
      <span class="company-mark__name">HARBORVIEW ESTATES LLC</span>
    </div>
    <div class="note-lines">
      <div class="note-line"></div>
      <div class="note-line"></div>
      <div class="note-line"></div>
      <div class="note-line"></div>
      <div class="note-line"></div>
      <div class="note-line"></div>
    </div>
  </section>
</body>
</html>
```